Accounting firm needing business card / letterhead designed
Marcus L. Trenholm, CPA
marcus@veltrowledger.com
www.veltrowledger.com
842 E Alder Ave Marlow Bend, IN 43827
419-562-0974

```html
<!DOCTYPE html>
<html lang="en">
<head>
<meta charset="utf-8">
<title>Veltrow Ledger – Business Card</title>
<link rel="stylesheet" href="https://fonts.googleapis.com/css2?family=Roboto:wght@400;500;700&family=Roboto+Condensed:wght@700&display=swap">
<style>
  :root {
    --backdrop: #e9e7e3;
    --card-white: #f6f6f5;
    --navy: #231f5c;
    --green: #84bd3e;
    --ink-grey: #4a4a4a;
    --white: #ffffff;
  }
  * { margin: 0; padding: 0; box-sizing: border-box; }
  html, body {
    width: 1200px;
    height: 960px;
    overflow: hidden;
    background: var(--backdrop);
  }
  .canvas {
    position: relative;
    width: 1200px;
    height: 960px;
  }
  .card {
    position: absolute;
    width: 600px;
    height: 343px;
    box-shadow: 0 2px 6px rgba(0,0,0,0.18);
  }
  /* Front */
  .card-front {
    left: 314px;
    top: 113px;
    background: var(--card-white);
  }
  .name-marker {
    position: absolute;
    left: 0;
    top: 47px;
    width: 15px;
    height: 39px;
    background: var(--navy);
  }
  .holder-name {
    position: absolute;
    left: 47px;
    top: 53px;
    font-family: "Roboto Condensed", "Arial Narrow", sans-serif;
    font-weight: 700;
    font-size: 21px;
    color: var(--navy);
    letter-spacing: 0.1px;
  }
  .address {
    position: absolute;
    left: 48px;
    top: 193px;
    font-family: "Roboto", Arial, sans-serif;
    font-size: 14px;
    line-height: 18px;
    color: var(--ink-grey);
  }
  .contact-list {
    position: absolute;
    left: 48px;
    top: 242px;
    list-style: none;
    font-family: "Roboto", Arial, sans-serif;
    font-size: 14px;
    color: var(--ink-grey);
  }
  .contact-list li {
    display: flex;
    align-items: center;
    height: 19px;
  }
  .contact-icon {
    width: 12px;
    height: 12px;
    margin-right: 10px;
    fill: var(--navy);
    flex: none;
  }
  .wordmark-front {
    position: absolute;
    right: 46px;
    top: 252px;
    font-family: "Roboto", Arial, sans-serif;
    font-weight: 700;
    font-size: 27px;
    letter-spacing: 0.5px;
    color: var(--navy);
    text-transform: uppercase;
    white-space: nowrap;
  }
  /* Back */
  .card-back {
    left: 311px;
    top: 472px;
    background: var(--navy);
  }
  .wordmark-back {
    position: absolute;
    left: 0;
    right: 0;
    top: 110px;
    text-align: center;
    font-family: "Roboto", Arial, sans-serif;
    font-weight: 700;
    font-size: 46px;
    letter-spacing: 2px;
    color: var(--white);
    text-transform: uppercase;
    white-space: nowrap;
  }
  .web-band {
    position: absolute;
    left: 0;
    top: 278px;
    width: 100%;
    height: 37px;
    background: var(--green);
    display: flex;
    align-items: center;
    justify-content: center;
    font-family: "Roboto", Arial, sans-serif;
    font-size: 14px;
    letter-spacing: 5px;
    color: var(--white);
  }
  .web-band strong { font-weight: 700; }
</style>
</head>
<body>
<main class="canvas">
  <section class="card card-front" aria-label="Business card front">
    <span class="name-marker"></span>
    <h1 class="holder-name">Marcus L. Trenholm, CPA</h1>
    <p class="address">842 E Alder Ave<br>Marlow Bend, IN 43827</p>
    <ul class="contact-list">
      <li>
        <svg class="contact-icon" viewBox="0 0 24 24" aria-hidden="true"><path d="M6.6 10.8a15.1 15.1 0 0 0 6.6 6.6l2.2-2.2a1 1 0 0 1 1-.25 11.4 11.4 0 0 0 3.6.57 1 1 0 0 1 1 1V20a1 1 0 0 1-1 1A17 17 0 0 1 3 4a1 1 0 0 1 1-1h3.5a1 1 0 0 1 1 1c0 1.25.2 2.45.57 3.570a1 1 0 0 1-.25 1z"/></svg>
        419-562-0974
      </li>
      <li>
        <svg class="contact-icon" viewBox="0 0 24 24" aria-hidden="true"><path d="M2 5h20v14H2z"/><path d="M3 6.5l9 7 9-7" stroke="var(--card-white)" stroke-width="1.6" fill="none"/></svg>
        marcus@veltrowledger.com
      </li>
      <li>
        <svg class="contact-icon" viewBox="0 0 24 24" aria-hidden="true"><circle cx="12" cy="12" r="10"/><path d="M7 7c2 1 3 0 4 2s-1 3 0 4 3 1 2 4M15 4c0 2 2 2 3 4" stroke="var(--card-white)" stroke-width="1.6" fill="none"/></svg>
        www.veltrowledger.com
      </li>
    </ul>
    <p class="wordmark-front">Veltrow Ledger</p>
  </section>

  <section class="card card-back" aria-label="Business card back">
    <p class="wordmark-back">Veltrow Ledger</p>
    <p class="web-band">www.<strong>veltrowledger</strong>.com</p>
  </section>
</main>
</body>
</html>
```